Webshop for furniture and lamps

We need a design for a web shop with APP that should have two options:
1-Webshop in general which should attract to private customer in general and
2-Website that is meant to attract big customers as hotels and restaurants who would have their own customerize login.

That's the idea behind the shop.

It should be diveded into 4 parts
vintage furniture
rattan set outdoor and indoor
lamps and
wooden wall decor

The name of the shop is loma vereda!

Please kindly make me an offer.

Reason: Dear designers, so far there hasn't been a design that really matched. Look up German web sites like www.glimmerhof-wohnen.de or www.sitzraum77.de... Haven't been convinced by designs! Sorry folks. Please submit some new ones. Kind regards Ned

```html
<!DOCTYPE html>
<html lang="en">
<head>
<meta charset="utf-8">
<title>Loma Vereda – Furniture &amp; Lamps</title>
<link href="https://fonts.googleapis.com/css2?family=Oswald:wght@400;500;700&family=Open+Sans:wght@400;600;700&display=swap" rel="stylesheet">
<style>
:root{
  --teal:#1fb5a6;
  --teal-dark:#17958a;
  --ink:#2b2b2b;
  --topbar:#2d2a28;
  --wood:#3b302a;
  --wood-light:#4a3d35;
  --grey-panel:#3d3b3a;
  --grey-soft:#f1f3f3;
  --red:#c9392f;
  --white:#ffffff;
  --muted:#555;
  --line:#bfbfbf;
}
*{box-sizing:border-box;margin:0;padding:0}
html,body{width:1200px;height:3692px;overflow:hidden}
body{position:relative;background:var(--white);font-family:"Open Sans",Arial,sans-serif;color:var(--ink);font-size:15px}
.abs{position:absolute}
.display{font-family:"Oswald","Arial Narrow",sans-serif;text-transform:uppercase;font-weight:700}

/* top bar */
.topbar{left:0;top:0;width:1200px;height:50px;background:var(--topbar);color:#ddd;font-size:13px;display:flex;align-items:center;padding:0 98px;justify-content:space-between}
.topbar nav{display:flex;gap:36px}

/* header */
.header{left:0;top:50px;width:1200px;height:120px;display:flex;align-items:center;justify-content:space-between;padding:0 98px}
.brand{display:flex;align-items:center;gap:14px}
.brand-mark{width:60px;height:44px;background:var(--ink)}
.brand-name{font-family:"Oswald",sans-serif;font-weight:700;font-size:36px;color:var(--teal);text-transform:uppercase;letter-spacing:.5px}
.mainnav{display:flex;gap:28px;font-family:"Oswald",sans-serif;font-weight:500;font-size:15px;text-transform:uppercase}

/* hero */
.hero{left:0;top:170px;width:1200px;height:430px;background:linear-gradient(90deg,#6d5c4c 0%,#8a7663 40%,#6f5a48 70%,#54433a 100%)}
.members{left:200px;top:250px;width:260px;text-align:center;color:#fff}
.members-icon{width:96px;height:96px;border-radius:50%;background:#fff;margin:0 auto 14px}
.members h3{font-family:"Oswald",sans-serif;font-size:30px;color:var(--teal);text-transform:uppercase}
.members p{font-size:13px;line-height:21px;margin-top:10px}
.members small{display:block;font-size:12px;margin-top:16px}
.signup{left:717px;top:210px;width:348px;height:360px;background:var(--teal);padding:38px 36px;color:#fff;text-align:center}
.signup h2{font-family:"Oswald",sans-serif;font-size:34px;line-height:40px;text-transform:uppercase}
.field{height:50px;background:#fff;color:#999;font-size:12px;display:flex;align-items:center;justify-content:center;margin-top:16px}
.signup h2+.field{margin-top:22px}
.btn-dark{height:50px;background:var(--ink);color:#fff;font-family:"Oswald",sans-serif;font-size:20px;display:flex;align-items:center;justify-content:center;margin-top:18px;text-transform:uppercase}
.signup-tab{left:872px;top:550px;width:40px;height:40px;border-radius:50%;background:#fff;border:10px solid var(--ink)}

/* section headings */
.boxhead{height:54px;border:3px solid var(--ink);display:flex;align-items:center;justify-content:center;font-family:"Oswald",sans-serif;font-weight:500;font-size:22px;text-transform:uppercase;letter-spacing:.5px;background:#fff}
.boxhead.on-dark{background:transparent;border-color:#fff;color:#fff}

.cats{left:0;top:782px;width:1200px;text-align:center;font-size:13px}
.cats .links{font-family:"Oswald",sans-serif;text-transform:uppercase;font-size:15px}
.cats .links b{color:var(--teal);font-weight:500}
.cats p{margin-top:6px;font-size:13px}
.readmore{font-family:"Oswald",sans-serif;font-weight:700;font-size:13px;text-transform:uppercase}
.cats .readmore{display:block;margin-top:22px}

.product{width:300px;text-align:center}
.product .photo{height:250px}
.product h4{font-family:"Oswald",sans-serif;font-size:17px;margin-top:40px;text-transform:uppercase}
.product h4::after{content:"";display:block;width:56px;height:2px;background:var(--ink);margin:12px auto 0}
.price{color:var(--red);font-family:"Oswald",sans-serif;font-size:18px;margin-top:12px}
.product p{font-size:13px;line-height:22px;margin-top:8px}
.shopnow{left:483px;top:1385px;width:234px;height:52px;background:var(--teal);color:#fff;font-family:"Oswald",sans-serif;font-size:24px;display:flex;align-items:center;justify-content:center;clip-path:polygon(0 0,100% 0,88% 100%,12% 100%)}

/* blog */
.blog{left:0;top:1530px;width:1200px;height:756px;background:linear-gradient(180deg,var(--wood) 0%,var(--wood-light) 50%,var(--wood) 100%)}
.news{width:300px;color:#fff}
.news-head{display:flex;align-items:center;gap:14px}
.num{width:44px;height:44px;background:var(--teal);color:#fff;font-family:"Oswald",sans-serif;font-size:28px;display:flex;align-items:center;justify-content:center}
.news-head h5{font-family:"Oswald",sans-serif;font-size:18px;text-transform:uppercase}
.news p{font-size:13px;line-height:20px;margin-top:12px;color:#eee}
.news .readmore{display:block;margin-top:10px}
.promo{left:98px;top:2163px;width:1004px;height:123px;display:flex}
.promo-photo{width:533px;background:linear-gradient(90deg,#b38f55,#d9c79d 50%,#9a7a4a)}
.promo-panel{flex:1;background:var(--teal);color:#fff;display:flex;align-items:center;justify-content:space-between;padding:0 40px 0 26px}
.promo-panel h3{font-family:"Oswald",sans-serif;font-size:34px;line-height:34px;text-transform:uppercase}
.promo-panel small{font-family:"Oswald",sans-serif;font-size:16px;text-transform:uppercase}
.btn-outline{border:3px solid #fff;padding:10px 16px;font-family:"Oswald",sans-serif;font-size:15px;text-transform:uppercase}

/* testimonial */
.portrait{left:98px;top:2474px;width:280px;height:218px;background:linear-gradient(180deg,#d8d2ca,#2a2626)}
.quote{left:378px;top:2474px;width:613px;height:218px;background:var(--grey-soft);padding:40px 30px}
.quote h5{font-family:"Oswald",sans-serif;font-size:18px}
.quote h5::after{content:"";display:block;width:56px;height:2px;background:var(--ink);margin-top:14px}
.quote p{font-size:13px;line-height:20px;margin-top:14px;color:var(--muted)}
.arrows{display:flex;gap:5px}
.arrows span{width:44px;height:44px;background:var(--teal);display:flex;align-items:center;justify-content:center}
.divider{left:98px;top:2758px;width:1004px;height:3px;background:#666}

.tweet{left:115px;top:2994px;width:500px}
.tweet h5{font-family:"Oswald",sans-serif;font-size:17px;text-transform:uppercase}
.tweet h5::after{content:"";display:block;width:56px;height:2px;background:var(--ink);margin-top:12px}
.tweet p{font-size:13px;line-height:20px;margin-top:12px;color:var(--muted)}
.tweet small{display:block;font-size:12px;margin-top:30px}
.tweet-line{left:115px;top:3163px;width:500px;height:3px;background:#666}
.video{left:680px;top:2951px;width:345px;height:219px;background:linear-gradient(160deg,#8a8f8c,#4d5550 60%,#6a5c4c)}

/* features */
.features{left:0;top:3240px;width:1200px;height:360px;background:var(--grey-panel)}
.feature{top:3240px;height:323px;border-right:1px solid #2c2b2a;background:#4a4847;text-align:center;color:#fff}
.feature-head{height:99px;background:var(--teal);display:flex;align-items:center;justify-content:center;gap:18px;font-family:"Oswald",sans-serif;font-size:20px;text-transform:uppercase}
.feature-head + .rule{width:50px;height:2px;background:#ddd;margin:26px auto 0}
.feature p{font-size:13px;line-height:20px;margin:16px auto 0;width:240px}
.cards{display:flex;gap:10px;justify-content:center;margin-top:12px}
.cards span{width:48px;height:30px;background:#fff;border-radius:3px}
.btn-small{display:inline-block;margin-top:22px;border:2px solid #fff;padding:6px 20px;font-family:"Oswald",sans-serif;font-size:13px;text-transform:uppercase}

.footer{left:0;top:3600px;width:1200px;height:92px;background:var(--topbar);color:#ccc;font-size:12px;display:flex;align-items:center;justify-content:space-between;padding:0 98px}
.footer nav{display:flex;gap:24px;margin-left:auto;margin-right:60px}
.social{display:flex;gap:8px}
.social span{width:26px;height:26px}
</style>
</head>
<body>

<div class="abs topbar">
  <span>Milo Harnett, welcome to our online store!</span>
  <nav><span>Login</span><span>My Account ▾</span><span>0 item</span><span>Checkout</span></nav>
</div>

<header class="abs header">
  <div class="brand"><span class="brand-mark"></span><span class="brand-name">Loma Vereda</span></div>
  <nav class="mainnav"><span>Home</span><span>Shop by Brand</span><span>Top Sellers</span><span>Clearance</span><span>Help Center</span><span>My Favorites</span>
    <svg width="16" height="16" viewBox="0 0 16 16"><circle cx="6.5" cy="6.5" r="4.5" fill="none" stroke="#2b2b2b" stroke-width="2"/><line x1="10" y1="10" x2="14" y2="14" stroke="#2b2b2b" stroke-width="2"/></svg>
  </nav>
</header>

<div class="abs hero" role="img" aria-label="Photo of a wooden interior with furniture"></div>
<div class="abs members">
  <div class="members-icon"></div>
  <h3>Members</h3>
  <p>Join us and choose your membership here:<br>for <b>Business Membership SIGN UP</b> here<br>Private <b>Customer Membership SIGN UP</b> here</p>
  <small>terms and conditions</small>
</div>
<div class="abs signup">
  <h2>Business Member<br>Sign Up Here</h2>
  <div class="field">type your name here</div>
  <div class="field">type your email here</div>
  <div class="btn-dark">Sign In</div>
</div>
<div class="abs signup-tab"></div>

<div class="abs boxhead" style="left:468px;top:680px;width:262px">Shop by Category</div>
<div class="abs cats">
  <div class="links">Vintage Furniture &nbsp;|&nbsp; <b>Rattan Set Outdoor and Indoor</b> &nbsp;|&nbsp; Lamps &nbsp;|&nbsp; Wooden Wall Decor</div>
  <p>sunt perspiciatis ipsam sed doloremque ipsam dolores totam unde aut illo sed veritatis explicabo dicta quia dicta veritatis dicta sunt quasi eaque rem</p>
  <span class="readmore">Read more</span>
</div>

<div class="abs product" style="left:120px;top:923px">
  <div class="photo" role="img" aria-label="Painted vintage chest of drawers" style="background:linear-gradient(180deg,#b86a3a,#8c4a36 60%,#5f6b7a)"></div>
  <h4>Voluptatem fugit aut</h4><div class="price">$876.00</div>
  <p>ipsum dolor sit amet <b>voluptatem</b> fugit aut<br>ut rerne rem ipsam quasi voluptatem</p>
</div>
<div class="abs product" style="left:450px;top:923px">
  <div class="photo" role="img" aria-label="Weathered wooden sideboard" style="background:linear-gradient(180deg,#fff 20%,#a99077 40%,#7f9c96 70%,#fff 85%)"></div>
  <h4>Voluptatem fugit aut</h4><div class="price">$876.00</div>
  <p>ipsum dolor sit amet voluptatem fugit aut<br>ut rerne <b>rem ipsam</b> quasi voluptatem</p>
</div>
<div class="abs product" style="left:780px;top:923px">
  <div class="photo" role="img" aria-label="Carved wooden cabinet with open door" style="background:linear-gradient(180deg,#8a5a3a,#5e3b26)"></div>
  <h4>Voluptatem fugit aut</h4><div class="price">$876.00</div>
  <p>ipsum <b>dolor sit</b> amet voluptatem fugit aut<br>ut rerne rem ipsam quasi voluptatem</p>
</div>
<div class="abs shopnow">SHOP NOW</div>

<section class="abs blog" role="img" aria-label="Dark wood texture background"></section>
<div class="abs boxhead on-dark" style="left:430px;top:1615px;width:340px">Lates News from Blog</div>

<div class="abs news" style="left:98px;top:1732px"><div class="news-head"><span class="num">1</span><h5>Amet voluptatem</h5></div><p>Lorem ipsum dolor sit amet rem illo omnis aperiam ab ipsam ipsa odit aut aperiam aspernatur veritatis unde enim accusantium laudantium laudantium sunt</p><span class="readmore">Read more</span></div>
<div class="abs news" style="left:452px;top:1732px"><div class="news-head"><span class="num">2</span><h5>Amet voluptatem</h5></div><p>Lorem ipsum dolor sit amet rem illo omnis aperiam ab ipsam ipsa odit aut aperiam aspernatur veritatis unde enim accusantium laudantium laudantium sunt</p><span class="readmore">Read more</span></div>
<div class="abs news" style="left:806px;top:1732px"><div class="news-head"><span class="num">3</span><h5>Amet voluptatem</h5></div><p>Lorem ipsum dolor sit amet rem illo omnis aperiam ab ipsam ipsa odit aut aperiam aspernatur veritatis unde enim accusantium laudantium laudantium sunt</p><span class="readmore">Read more</span></div>
<div class="abs news" style="left:98px;top:1938px"><div class="news-head"><span class="num">4</span><h5>Amet voluptatem</h5></div><p>Lorem ipsum dolor sit amet rem illo omnis aperiam ab ipsam ipsa odit aut aperiam aspernatur veritatis unde enim accusantium laudantium laudantium sunt</p><span class="readmore">Read more</span></div>
<div class="abs news" style="left:452px;top:1938px"><div class="news-head"><span class="num">5</span><h5>Amet voluptatem</h5></div><p>Lorem ipsum dolor sit amet rem illo omnis aperiam ab ipsam ipsa odit aut aperiam aspernatur veritatis unde enim accusantium laudantium laudantium sunt</p><span class="readmore">Read more</span></div>
<div class="abs news" style="left:806px;top:1938px"><div class="news-head"><span class="num">6</span><h5>Amet voluptatem</h5></div><p>Lorem ipsum dolor sit amet rem illo omnis aperiam ab ipsam ipsa odit aut aperiam aspernatur veritatis unde enim accusantium laudantium laudantium sunt</p><span class="readmore">Read more</span></div>

<div class="abs promo">
  <div class="promo-photo" role="img" aria-label="Rattan outdoor sofa with striped cushions"></div>
  <div class="promo-panel"><div><h3>Outside Furniture</h3><small>Big savings on quality items</small></div><span class="btn-outline">Shop now</span></div>
</div>

<div class="abs boxhead" style="left:468px;top:2357px;width:264px">What They Says</div>
<div class="abs portrait" role="img" aria-label="Portrait photo of a customer in a suit"></div>
<div class="abs quote">
  <h5>TOMAS REYL, 25 YO</h5>
  <p>Lorem ipsum dolor sit amet rem rem illo omnis aperiam ab ipsam ipsa odit aut aperiam aspernatur veritatis unde sed, sed enim accusantium laudantium sunt perspiciatis ipsam sed doloremque ....</p>
</div>
<div class="abs arrows" style="left:1009px;top:2474px">
  <span><svg width="14" height="18" viewBox="0 0 14 18"><path d="M11 2 L4 9 L11 16" fill="none" stroke="#fff" stroke-width="3"/></svg></span>
  <span><svg width="14" height="18" viewBox="0 0 14 18"><path d="M3 2 L10 9 L3 16" fill="none" stroke="#fff" stroke-width="3"/></svg></span>
</div>
<div class="abs divider"></div>

<div class="abs boxhead" style="left:246px;top:2837px;width:234px">Recent Tweets</div>
<div class="abs boxhead" style="left:720px;top:2837px;width:262px">Watch Our Video</div>
<div class="abs arrows" style="left:523px;top:2951px">
  <span><svg width="14" height="18" viewBox="0 0 14 18"><path d="M11 2 L4 9 L11 16" fill="none" stroke="#fff" stroke-width="3"/></svg></span>
  <span><svg width="14" height="18" viewBox="0 0 14 18"><path d="M3 2 L10 9 L3 16" fill="none" stroke="#fff" stroke-width="3"/></svg></span>
</div>
<div class="abs tweet">
  <h5>Tomas Reyl @ Milo Harnett</h5>
  <p>Lorem ipsum dolor sit amet rem rem illo omnis aperiam ab ipsam ipsa odit aut aperiam aspernatur veritatis unde sed, sed enim accusan ipsam sed doloremque ....</p>
  <small>retweeted by <b>Ina Velde</b></small>
</div>
<div class="abs tweet-line"></div>
<div class="abs video" role="img" aria-label="Video still of black rattan chairs on a terrace"></div>
<svg class="abs" style="left:826px;top:3034px" width="54" height="54" viewBox="0 0 54 54"><circle cx="27" cy="27" r="27" fill="#fff"/><path d="M21 16 L39 27 L21 38 Z" fill="#2b2b2b"/></svg>

<section class="abs features"></section>
<div class="abs feature" style="left:98px;width:333px">
  <div class="feature-head"><svg width="34" height="34" viewBox="0 0 34 34"><rect x="4" y="8" width="22" height="22" fill="none" stroke="#fff" stroke-width="3"/><path d="M10 14 L17 6 L30 10 L26 24" fill="none" stroke="#fff" stroke-width="3"/></svg>Payment Method</div>
  <div class="rule"></div>
  <p>Lorem ipsum dolor sit amet rem illo omnis</p>
  <div class="cards"><span></span><span></span><span></span><span></span></div>
  <span class="btn-small">Read more</span>
</div>
<div class="abs feature" style="left:431px;width:338px">
  <div class="feature-head"><svg width="40" height="30" viewBox="0 0 40 30"><rect x="2" y="4" width="22" height="16" fill="#fff"/><path d="M24 9 H32 L38 15 V20 H24 Z" fill="#fff"/><circle cx="9" cy="24" r="4" fill="#fff"/><circle cx="31" cy="24" r="4" fill="#fff"/></svg>Free Shipping</div>
  <div class="rule"></div>
  <p>Lorem ipsum dolor sit amet rem illo omnis aperiam ab ipsam ipsa odit aut aperiam aspernatur veritatis unde enim accusantium</p>
  <span class="btn-small">Read more</span>
</div>
<div class="abs feature" style="left:769px;width:333px;border-right:none">
  <div class="feature-head"><svg width="30" height="36" viewBox="0 0 30 36"><path d="M8 16 V10 a7 7 0 0 1 14 0 V16" fill="none" stroke="#fff" stroke-width="4"/><rect x="3" y="16" width="24" height="18" fill="#fff"/></svg>Secure Shopping</div>
  <div class="rule"></div>
  <p>Lorem ipsum dolor sit amet rem illo omnis aperiam ab ipsam ipsa odit aut aperiam aspernatur veritatis unde enim accusantium</p>
  <span class="btn-small">Read more</span>
</div>

<footer class="abs footer">
  <span>© 2016 <b>LOMA VEREDA GMBH</b>. ALL RIGHTS RESERVED.</span>
  <nav><span>ABOUT US</span><span>TERM AND USE</span><span>PRIVACY POLICY</span><span>FAQS</span><span>CONTACT US</span></nav>
  <div class="social"><span style="background:#3b5998"></span><span style="background:#1da1f2"></span><span style="background:#d93025"></span><span style="background:#0e76a8"></span><span style="background:#c8232c"></span></div>
</footer>

</body>
</html>
```